The BRV Relational Philanthropy Cycle

The title for this graphic is above. It must be included.
I am looking for a graphic representation of the relationship between the Christian school and the donor / pointing to the child (student) - the school's mission / outcome of investment through a gift / appreciation of the gift / communication of the gift impact for the child / stronger relationship going back to the child. This is not easy to do. I've tried to do it on my own and can't get it.
Any cliched child representations will be dismissed out of hand e.g. mortar boards, pencils, uniforms etc. The child should be abstract so that gender and race are irrelevant.
The key to this whole thing is the idea of RELATIONSHIP. The close relationship of donor and the Christian school, the pointing of that relationship to focus on the child / the school's mission, the outpouring of generosity that then happens in the heart of the donor and the gift that results, followed up by intentional work by the Christian school to thank and inform the donor - thank for the gift inform about the gift's expenditure and impact in the life of the child - all of which leads to a strengthening of the relationship and continued philanthropy as a never ending cycle.
It must be branded - logo and colors attached.
It must be obvious - easy to grasp the basic idea of relationship resulting in generosity / philanthropy. The visual should be clear - any words used illustrate - I should not 'need' the words to understand the idea.
I need it on a PP slide, jpeg, thumbnail. It must be highly legible in no more than 1/3 of a regular size piece of paper.
Our website is faithacademyworks.example
google donor cultivation cycle or donor giving cycle to see many examples of cycles that are used in secular contexts - the big difference in BRV's is the focus on the child and the importance of the relationship.

```html
<!DOCTYPE html>
<html lang="en">
<head>
<meta charset="utf-8">
<title>The BRV Relational Philanthropy Cycle</title>
<link rel="stylesheet" href="https://fonts.googleapis.com/css2?family=Crimson+Text:wght@400;600;700&family=Montserrat:wght@500;600;700&display=swap">
<style>
  :root {
    --bg: #ffffff;
    --brand-blue: #3f72a8;
    --brand-blue-text: #3b70a9;
    --title-grey: #6d6d6d;
    --arrow-grey: #8e8e8e;
    --ring-grey: #dddddd;
    --ink: #1e1e1e;
    --white: #ffffff;
  }
  * { margin: 0; padding: 0; box-sizing: border-box; }
  html, body {
    width: 1200px;
    height: 849px;
    overflow: hidden;
    background: var(--bg);
  }
  .canvas {
    position: relative;
    width: 1200px;
    height: 849px;
  }
  .title {
    position: absolute;
    left: 125px;
    top: 104px;
    font-family: "Crimson Text", Georgia, serif;
    font-weight: 600;
    font-size: 34px;
    color: var(--title-grey);
    letter-spacing: 0.1px;
  }
  .title .brand-name {
    color: var(--brand-blue);
    font-weight: 700;
  }
  .brand-mark {
    position: absolute;
    left: 880px;
    top: 118px;
    font-family: "Crimson Text", Georgia, serif;
    font-weight: 600;
    font-size: 62px;
    line-height: 1;
    color: var(--brand-blue);
    letter-spacing: 1px;
  }
  .cycle {
    position: absolute;
    left: 0;
    top: 0;
  }
  .node-label {
    font-family: "Montserrat", Arial, sans-serif;
    font-weight: 700;
    font-size: 18px;
    fill: var(--white);
    text-anchor: middle;
  }
  .ring-label {
    font-family: "Montserrat", Arial, sans-serif;
    font-weight: 600;
    font-size: 17px;
    fill: var(--ink);
  }
  .flow-label {
    font-family: "Montserrat", Arial, sans-serif;
    font-weight: 600;
    font-size: 21px;
    fill: var(--brand-blue-text);
  }
  .icon {
    fill: none;
    stroke: var(--white);
    stroke-width: 2.2;
    stroke-linecap: round;
    stroke-linejoin: round;
  }
</style>
</head>
<body>
<div class="canvas">
  <h1 class="title"><span class="brand-name">BRV</span> Relational Philanthropy Cycle</h1>
  <div class="brand-mark">BRV</div>

  <svg class="cycle" width="1200" height="849" viewBox="0 0 1200 849" aria-label="Relational philanthropy cycle: donor, child and Christian school">
    <defs>
      <marker id="arrowhead" viewBox="0 0 10 10" refX="2" refY="5" markerWidth="2.6" markerHeight="2.6" orient="auto" markerUnits="strokeWidth">
        <path d="M0,0 L10,5 L0,10 Z" fill="var(--arrow-grey)"/>
      </marker>
      <path id="path-outpouring" d="M325,455 A260,260 0 0 1 845,455"/>
      <path id="path-impact" d="M307,455 A278,278 0 0 0 863,455"/>
      <path id="path-focus" d="M479,455 A106,106 0 0 1 691,455"/>
      <path id="path-mission" d="M463,455 A122,122 0 0 0 707,455"/>
    </defs>

    <!-- flow arrows -->
    <path class="flow-arrow" d="M379,336 A238,238 0 0 1 758,331" fill="none" stroke="var(--arrow-grey)" stroke-width="27" marker-end="url(#arrowhead)"/>
    <path class="flow-arrow" d="M791,574 A238,238 0 0 1 406,612" fill="none" stroke="var(--arrow-grey)" stroke-width="27" marker-end="url(#arrowhead)"/>

    <text class="flow-label"><textPath href="#path-outpouring" startOffset="50%" text-anchor="middle">The Outpouring Of Generosity</textPath></text>
    <text class="flow-label"><textPath href="#path-impact" startOffset="50%" text-anchor="middle">Impact In The Life Of The Child</textPath></text>

    <!-- shared focus ring -->
    <circle class="focus-ring" cx="585" cy="455" r="158" fill="var(--ring-grey)"/>
    <text class="ring-label"><textPath href="#path-focus" startOffset="50%" text-anchor="middle">Focus On The Child</textPath></text>
    <text class="ring-label"><textPath href="#path-mission" startOffset="50%" text-anchor="middle">The School's Mission</textPath></text>

    <!-- donor -->
    <g class="node node-donor">
      <circle cx="405" cy="455" r="92" fill="var(--brand-blue)"/>
      <path class="icon" d="M405,432 C398,425 389,427 389,435 C389,441 397,446 405,452 C413,446 421,441 421,435 C421,427 412,425 405,432 Z"/>
      <path class="icon" d="M383,460 L393,460 C397,460 401,463 405,463 L414,463 C417,463 417,467 414,467 L402,467 M414,466 L425,459 C428,457 431,460 429,463 L419,472 C416,474 412,475 408,475 L393,475 L383,471"/>
      <text class="node-label" x="405" y="503">DONOR</text>
    </g>

    <!-- child -->
    <g class="node node-child">
      <circle cx="585" cy="455" r="92" fill="var(--brand-blue)"/>
      <circle class="icon" cx="585" cy="426" r="5"/>
      <path class="icon" d="M578,452 L578,442 C578,437 592,437 592,442 L592,452 L589,452 L589,466 L581,466 L581,452 Z"/>
      <circle class="icon" cx="567" cy="432" r="4"/>
      <path class="icon" d="M562,455 L562,446 C562,442 572,442 572,446 L572,455 L570,455 L570,466 L564,466 L564,455 Z"/>
      <circle class="icon" cx="603" cy="432" r="4"/>
      <path class="icon" d="M598,455 L598,446 C598,442 608,442 608,446 L608,455 L606,455 L606,466 L600,466 L600,455 Z"/>
      <text class="node-label" x="585" y="503">THE CHILD</text>
    </g>

    <!-- christian school -->
    <g class="node node-school">
      <circle cx="765" cy="455" r="92" fill="var(--brand-blue)"/>
      <path class="icon" d="M765,412 L765,424 M760,417 L770,417"/>
      <path class="icon" d="M755,436 L765,424 L775,436 L775,466 L755,466 Z"/>
      <path class="icon" d="M755,446 L745,446 L745,466 L755,466 M775,446 L785,446 L785,466 L775,466"/>
      <path class="icon" d="M761,466 L761,454 L769,454 L769,466"/>
      <text class="node-label" x="765" y="487">CHRISTIAN</text>
      <text class="node-label" x="765" y="510">SCHOOL</text>
    </g>
  </svg>
</div>
</body>
</html>
```